Bluefinch Painting needs a Website

We need a website built for a Painting company I own, we mainly do residential painting, but don't want to be limited to that.

Need to have estimate request form.
Need pic's of past projects

I like the look of the website for http://www.harbor-brushworks.com
& "Westlake Home inspections"

My logo that was designed here on ArtHatch on the front page

I would like one of the houses I downloaded as part of the background
of the front page.

Target Market(s)

Home owners

Industry/Entity Type

Painting

Number of Pages Required

1 page

Font styles to use
Serif

Requirements
Must have
• Estimate request form for home owners to fill out -
• Name:
• Phone Number:
• Address:
• E-mail:
• Painting project description:
• And my info to:
• My phone number: (555) 318-7046
• My web address bluefinchpainting.example
Nice to have
• My logo that was designed here on ArtHatch

```html
<!DOCTYPE html>
<html lang="en">
<head>
<meta charset="utf-8">
<title>Bluefinch Painting</title>
<link href="https://fonts.googleapis.com/css2?family=Crimson+Text:wght@400;600&family=Roboto+Condensed:wght@500&family=Arimo:wght@400;700&display=swap" rel="stylesheet">
<style>
:root{
  --blue:#1e7ec8;
  --blue-dark:#166aa9;
  --ink:#222;
  --text:#333;
  --black:#0d0d0d;
  --footer:#1b1b1b;
  --line:#bbb;
  --white:#fff;
}
*{box-sizing:border-box;margin:0;padding:0}
html,body{width:930px;height:1200px;overflow:hidden;background:var(--white)}
body{position:relative;font-family:Arimo,Arial,sans-serif;color:var(--text)}
.abs{position:absolute}
.serif{font-family:"Crimson Text",Georgia,serif}

.logo{left:123px;top:16px;display:flex;align-items:center;gap:10px}
.logo-mark{width:34px;height:34px;background:var(--blue)}
.logo-name{font-family:"Crimson Text",Georgia,serif;font-size:27px;color:var(--ink);letter-spacing:1px}
.truck{left:503px;top:8px;width:151px;height:70px;background:linear-gradient(#f2f2f2,#cfd4d8);border:1px solid #ccc}
.estimate-btn{left:680px;top:3px;width:116px;height:23px;background:var(--blue);color:var(--white);font-family:"Roboto Condensed",sans-serif;font-size:14px;text-align:center;line-height:23px}
.call{left:682px;top:40px;display:flex;gap:8px;align-items:center}
.call small{display:block;font-size:11px;color:var(--ink)}
.call strong{display:block;font-size:15px;font-weight:400;color:var(--ink)}

.nav{left:0;top:78px;width:930px;height:31px;background:var(--blue)}
.nav a{position:absolute;top:0;height:31px;line-height:31px;text-align:center;color:var(--white);text-decoration:none;font-family:"Crimson Text",Georgia,serif;font-size:13px;border-right:1px solid rgba(255,255,255,.35)}
.nav a.active{background:var(--black);font-weight:600}

.hero{left:0;top:109px;width:930px;height:273px;background:linear-gradient(180deg,#5d6672 0%,#8c7660 45%,#6b5140 75%,#3f4a2e 100%)}
.arrow{width:28px;height:28px;border-radius:50%;background:rgba(0,0,0,.6);top:216px}
.tagline{left:0;top:382px;width:930px;height:35px;background:#161616;color:var(--white);text-align:center;line-height:35px;font-size:17px;font-family:"Crimson Text",Georgia,serif;letter-spacing:.3px}
.welcome{left:0;top:417px;width:930px;height:167px;background:linear-gradient(90deg,#6a6d70,#55585b 50%,#6b6e70)}
.welcome h2{position:absolute;left:0;width:930px;top:18px;text-align:center;color:var(--white);font-weight:400;font-size:17px}
.welcome p{position:absolute;left:138px;width:654px;top:68px;text-align:center;color:var(--white);font-size:9.5px;line-height:17px}
.btn{background:var(--black);color:var(--white);font-size:10px;text-align:center;display:block}

.col h3{font-family:"Crimson Text",Georgia,serif;font-weight:400;font-size:18px;color:var(--ink)}
.photo{border:2px solid #ddd}
.col p{font-size:9.5px;line-height:14.5px}
.field{left:609px;width:198px;height:20px;border:1px solid #bbb;border-radius:2px;font-size:8.5px;font-style:italic;color:#666;padding:5px 8px}

.gallery-title{left:186px;top:893px;font-size:17px;color:var(--ink)}
.thumb{top:939px;width:120px;height:95px;border:1px solid #666;padding:3px;background:var(--white)}
.thumb div{width:100%;height:100%;position:relative}
.thumb span{position:absolute;left:0;bottom:0;width:100%;background:rgba(0,0,0,.7);color:var(--white);font-family:"Crimson Text",Georgia,serif;font-size:12px;padding:1px 6px}

.footer{left:0;top:1041px;width:930px;height:133px;background:var(--footer);color:var(--white)}
.footer h4{position:absolute;top:15px;font-size:9.5px;font-weight:700;padding-bottom:2px;border-bottom:1px dashed #777}
.footer ul{position:absolute;list-style:none;font-size:9px;line-height:15.4px}
.bar{left:0;top:1174px;width:930px;height:26px;background:var(--blue);color:var(--white);text-align:center;line-height:26px;font-size:9px}
</style>
</head>
<body>

<header>
  <div class="abs logo"><span class="logo-mark"></span><span class="logo-name">BLUEFINCH PAINTING</span></div>
  <div class="abs truck" role="img" aria-label="Company trailer with logo"></div>
  <a class="abs estimate-btn">Free Estimates</a>
  <div class="abs call">
    <svg width="22" height="22" viewBox="0 0 22 22"><circle cx="11" cy="11" r="10" fill="none" stroke="#1e7ec8" stroke-width="1.5"/><path d="M8 6c-2 2-1 7 3 10l2-2-2-2-1 1c-1-1-2-3-2-4l1-1z" fill="#1e7ec8"/></svg>
    <div><small>Call Us Today</small><strong>555-318-7046</strong></div>
  </div>
</header>

<nav class="abs nav">
  <a class="active" style="left:125px;width:57px">Home</a>
  <a style="left:182px;width:90px">About Us</a>
  <a style="left:272px;width:80px">Exterior</a>
  <a style="left:352px;width:77px">Interior</a>
  <a style="left:429px;width:97px">Residential</a>
  <a style="left:526px;width:102px">Commerical</a>
  <a style="left:628px;width:104px">Past Projects</a>
  <a style="left:732px;width:96px;border-right:0">Contact Us</a>
</nav>

<section>
  <div class="abs hero" role="img" aria-label="Large two-storey stucco and brick house with white trimmed windows"></div>
  <svg class="abs arrow" style="left:89px" viewBox="0 0 28 28"><path d="M16 8l-6 6 6 6" stroke="#fff" fill="none" stroke-width="1.5"/></svg>
  <svg class="abs arrow" style="left:814px" viewBox="0 0 28 28"><path d="M12 8l6 6-6 6" stroke="#fff" fill="none" stroke-width="1.5"/></svg>
  <div class="abs tagline">PROVIDING QUALITY WORK AT AFFORDABLE PRICES</div>
  <div class="abs welcome" role="img" aria-label="Company trucks and trailers parked in front of a house">
    <h2 class="serif">Welcome to Bluefinch Painting</h2>
    <svg class="abs" style="left:339px;top:45px" width="268" height="10"><path d="M0 2h268M0 6h268" stroke="#fff" stroke-width="1"/><path d="M130 0l4 8 4-8" stroke="#fff" fill="none"/></svg>
    <p>Lorem ipsum dolor sit amet, consectetuer adipiscing elit, sed diam nonummy nibh euismod rent ut laoreet dolore magna aliquam erat volutpat. Ut wisi enim ad minim veniam, quis nostrud lore xererci tation ullamcorper suscipit lobortis nisl ut aliquip ex ea commodo consequat. Duis autem revel eum iriure dolor in hendrerit in vulputate velit esse molestie consequat.</p>
    <svg class="abs" style="left:375px;top:131px" width="186" height="12"><path d="M0 6h50M136 6h50M48 3h12M48 9h12M126 3h12M126 9h12" stroke="#fff"/></svg>
    <a class="abs btn" style="left:434px;top:128px;width:61px;height:18px;line-height:18px">Read More</a>
  </div>
</section>

<main>
  <div class="abs col" style="left:133px;top:600px;width:210px">
    <h3>Residential Painting</h3>
    <div class="photo" role="img" aria-label="Painter on ladder painting a house exterior" style="margin-top:9px;height:131px;background:linear-gradient(#3d4a2c,#8a8f7a 60%,#4a4a3e)"></div>
    <p style="margin-top:8px">Sed ut perspiciatis unde omnis iste natus error sit voluptatem accusantium doloremque laudantium, totam rem aperiam.</p>
    <a class="btn" style="margin-top:9px;width:61px;height:18px;line-height:18px">Read More</a>
  </div>
  <div class="abs col" style="left:370px;top:600px;width:210px">
    <h3>Commerical Painting</h3>
    <div class="photo" role="img" aria-label="Painter in white overalls rolling paint on an interior wall" style="margin-top:9px;height:131px;background:linear-gradient(90deg,#e5e4df,#f4f3ef 70%,#1b2a44 90%)"></div>
    <p style="margin-top:8px;padding-left:3px">Sed ut perspiciatis unde omnis iste natus error sit voluptatem accusantium doloremque laudantium, totam rem aperiam.</p>
    <a class="btn" style="margin-top:9px;margin-left:3px;width:61px;height:18px;line-height:18px">Read More</a>
  </div>
  <div class="abs col" style="left:607px;top:600px;width:203px">
    <h3>Quick Inquiry</h3>
    <div style="margin-top:4px;border-top:1px dashed var(--line)"></div>
  </div>
  <form>
    <div class="abs field" style="top:637px">Name</div>
    <div class="abs field" style="top:665px">Email</div>
    <div class="abs field" style="top:694px">Phone</div>
    <div class="abs field" style="top:723px">Type of Work</div>
    <div class="abs field" style="top:753px;height:58px">Message</div>
    <a class="abs btn" style="left:613px;top:819px;width:61px;height:18px;line-height:18px;font-weight:700">Submit</a>
  </form>

  <div class="abs" style="left:133px;top:865px;width:675px;height:1px;background:linear-gradient(90deg,transparent,#ccc,transparent)"></div>

  <svg class="abs" style="left:136px;top:884px" width="41" height="41"><circle cx="20.5" cy="20.5" r="19.5" fill="#fff" stroke="#ccc"/><rect x="13" y="14" width="14" height="13" rx="2" fill="var(--blue)"/><rect x="17" y="18" width="6" height="5" fill="#fff"/></svg>
  <h3 class="abs serif gallery-title" style="font-weight:400">Our Work Gallery</h3>
  <svg class="abs" style="left:770px;top:898px" width="32" height="14"><rect width="13" height="13" fill="#111"/><path d="M8 3l-4 3.5 4 3.5" stroke="#fff" fill="none" stroke-width="1.5"/><rect x="17" width="13" height="13" fill="var(--blue)"/><path d="M22 3l4 3.5-4 3.5" stroke="#fff" fill="none" stroke-width="1.5"/></svg>

  <div class="abs thumb" style="left:139px"><div role="img" aria-label="Painted house with garden" style="background:linear-gradient(#4d8ed0,#8b7a6c 50%,#4a6a32)"><span>Exterior Painting 1</span></div></div>
  <div class="abs thumb" style="left:273px"><div role="img" aria-label="Painter working on house siding" style="background:linear-gradient(#3a7fc8,#c8ccd6 50%,#9ea3ad)"><span>Exterior Painting 2</span></div></div>
  <div class="abs thumb" style="left:407px"><div role="img" aria-label="Painter on scaffold painting a wall" style="background:linear-gradient(#d8c99a,#e8e2cf 60%,#bdb49a)"><span>Exterior Painting 3</span></div></div>
  <div class="abs thumb" style="left:541px"><div role="img" aria-label="Stucco house with lawn and palms" style="background:linear-gradient(#a7c6e0,#c9b79a 50%,#5c8c3a)"><span>Exterior Painting 4</span></div></div>
  <div class="abs thumb" style="left:674px"><div role="img" aria-label="Two-storey grey house with patio" style="background:linear-gradient(#8a8d8f,#6d6a62 50%,#4f4a40)"><span>Exterior Painting 5</span></div></div>
</main>

<footer class="abs footer">
  <h4 style="left:133px">Quick Links</h4>
  <ul style="left:133px;top:36px">
    <li>• Home</li><li>• About Us</li><li>• Services</li><li>• Past Projects</li><li>• Contact Us</li>
  </ul>
  <h4 style="left:290px">Contact Information</h4>
  <ul style="left:292px;top:34px;line-height:13.5px">
    <li style="display:flex;gap:14px"><b>A:</b><span>Bluefinch Painting<br>Street Name City Name<br>State Zipcode</span></li>
    <li style="display:flex;gap:15px;margin-top:8px"><b>P:</b><span>555-318-7046</span></li>
    <li style="display:flex;gap:15px;margin-top:5px"><b>E:</b><span>inquiry@bluefinchpainting.example</span></li>
  </ul>
  <h4 style="left:472px">Work Times</h4>
  <ul style="left:474px;top:38px;line-height:22px">
    <li>◷&nbsp;&nbsp;Our work timings are:</li>
    <li>◷&nbsp;&nbsp;Monday - Friday. 8AM - 8PM</li>
    <li>◷&nbsp;&nbsp;Saturday:9AM - 4PM</li>
    <li>◷&nbsp;&nbsp;Sunday: closed</li>
  </ul>
  <div class="abs" style="left:660px;top:29px;display:flex;align-items:center;gap:6px"><span style="width:18px;height:18px;background:#fff"></span><span class="serif" style="font-size:14px">BLUEFINCH PAINTING</span></div>
  <div class="abs" style="left:690px;top:64px;width:84px;text-align:center;font-size:9.5px">We Accept</div>
  <div class="abs" style="left:673px;top:81px;display:flex;gap:3px">
    <span style="width:21px;height:14px;background:#2a5fa8;border-radius:2px"></span>
    <span style="width:21px;height:14px;background:#e8e8e8;border-radius:2px"></span>
    <span style="width:21px;height:14px;background:#f2f2f2;border-radius:2px"></span>
    <span style="width:21px;height:14px;background:#3c9ad6;border-radius:2px"></span>
    <span style="width:21px;height:14px;background:#c8372d;border-radius:2px"></span>
  </div>
</footer>
<div class="abs bar">Copyright ©2015, BluefinchPainting &nbsp;All Rights Reserved</div>

</body>
</html>
```